body therapist

I need to offer my services as a massage therapist at home, acclimating customer space aroma candles with music and everything else to bring comfort. 8 offer rituals like this: relaxing ritual, purifying ritual, ritual breast, facial and body cleansing ritual organic, ritual man, ritual feet, slimming ritual. Naraja handling colors, seawater, green, lavender

Target Market(s)

men and women, tired, stressed, looking for something new

Font styles to use
Decorative
Script

Colors
f37122
0493ce
abd037

Requirements
Must have
• detailing each massage
Nice to have
• simple and elegant

```html
<!DOCTYPE html>
<html lang="es">
<head>
<meta charset="utf-8">
<title>Serenia Spa – Masajes</title>
<link rel="stylesheet" href="https://fonts.googleapis.com/css2?family=Great+Vibes&family=Questrial&family=Cutive&family=Shadows+Into+Light+Two&display=swap">
<style>
  :root{
    --backdrop:#c9c9c9;
    --paper:#ffffff;
    --lime:#abd037;
    --orchid:#c95ec9;
    --ink:#6a6a6a;
    --ink-dark:#4a4a4a;
    --tab:#e2e2e2;
    --panel-top:#d4d5d8;
    --panel-bottom:#ffffff;
    --panel-edge:#b8b9bc;
  }
  *{margin:0;padding:0;box-sizing:border-box}
  html,body{width:1000px;height:1200px;overflow:hidden;background:var(--backdrop)}
  .canvas{position:relative;width:1000px;height:1200px}
  .page{
    position:absolute;left:108px;top:43px;width:785px;height:1112px;
    background:var(--paper);overflow:hidden;
    box-shadow:3px 4px 10px rgba(0,0,0,.35);
  }
  .page-tab{
    position:absolute;left:347px;top:0;width:90px;height:58px;
    background:var(--tab);border-radius:0 0 45px 45px;
    font:20px "Questrial",sans-serif;color:#333;text-align:center;line-height:66px;
  }
  .brand-title{
    position:absolute;left:0;top:70px;width:785px;text-align:center;
    font:86px/1 "Great Vibes",cursive;color:var(--lime);
  }
  .intro{
    position:absolute;left:37px;top:170px;width:715px;
    font:18.5px/23px "Questrial",sans-serif;color:var(--ink);
    letter-spacing:.35px;text-align:justify;
  }
  .art{position:absolute;left:0;top:0}
  .menu-panel{
    position:absolute;left:397px;top:299px;width:303px;height:746px;
    background:linear-gradient(180deg,var(--panel-top),var(--panel-bottom) 85%);
    border:1px solid var(--panel-edge);
    overflow:hidden;
  }
  .menu-title{
    position:absolute;left:14px;top:42px;width:280px;
    font:43px/1 "Cutive",serif;color:var(--orchid);letter-spacing:0;
    white-space:nowrap;
  }
  .service-list{list-style:none;position:absolute;left:18px;top:128px;width:280px}
  .service-list li{
    position:absolute;left:22px;width:250px;
    font:25px/30px "Shadows Into Light Two",cursive;color:var(--ink-dark);
    font-style:italic;
  }
  .service-list li::before{
    content:"";position:absolute;left:-22px;top:10px;width:12px;height:12px;
    background:var(--orchid);
  }
  .duration-badge{
    position:absolute;left:529px;top:929px;width:256px;height:78px;
    background:var(--lime);color:#fff;
    font:27px/78px "Questrial",sans-serif;text-align:center;
  }
</style>
</head>
<body>
<div class="canvas">
  <div class="page">
    <div class="page-tab">3</div>
    <h1 class="brand-title">Serenia Spa</h1>
    <p class="intro">Un espacio para tu CUERPO, MENTE Y ESPIRITU...<br>SERENIA es una empresa dedicada a brindar bienestar al ser sin salir de casa; transformando tu espacio con innovadoras técnicas de masajes, terapias y rituales para así llegar al máximo nivel de relajación del zen.</p>

    <svg class="art" width="785" height="1112" viewBox="0 0 785 1112">
      <defs>
        <linearGradient id="photoTone" x1="0" y1="0" x2="0.6" y2="1">
          <stop offset="0" stop-color="#f3c27a"/>
          <stop offset="0.4" stop-color="#f0a070"/>
          <stop offset="0.75" stop-color="#e89a78"/>
          <stop offset="1" stop-color="#f2e9ea"/>
        </linearGradient>
      </defs>
      <rect class="green-band" x="22" y="364" width="733" height="570" fill="var(--lime)"/>
      <path role="img" aria-label="Fotografía: mujer relajada recibiendo un masaje en la espalda" d="M0,454 Q460,430 785,930 L785,1112 L0,1112 Z" fill="url(#photoTone)"/>
    </svg>

    <div class="menu-panel">
      <h2 class="menu-title">MASAJES</h2>
      <ul class="service-list">
        <li style="top:0">MASAJE ZEN CON PIEDRAS SOLANA</li>
        <li style="top:90px">MASAJE AROMÁTICO</li>
        <li style="top:148px">MASAJE A CUATRO MANOS</li>
        <li style="top:239px">MASAJE RELAJANTE</li>
        <li style="top:297px">MASAJE REDUCTOR</li>
        <li style="top:361px">MASAJES PARA PIES</li>
        <li style="top:424px">MASAJES PARA EL</li>
      </ul>
    </div>

    <div class="duration-badge">DE 60-90 MINUTES</div>
  </div>
</div>
</body>
</html>
```